Stationery Set for Velmora Company

I need to create full stationery design for my company; Business Cards, Envelops, Letter Heads, Calendar.
In the letter head and Envelops... only contact information and website links.
Our company is a Service Management company with different domains of innovative services including Technology Service Management, Education Services, Outsourcing Management, Events Management.
I need a modern and innovative design specially for the business card. I some transparent designs and I like it, but don't limit your innovation to what I mentioned. Sky is limit for your innovation.

Target Market(s)

Middle East & Africa

Industry/Entity Type

Business Management

Colors
34a7d8
0355a3
85acd3
86cae7
cee9f5
cfdeed
e4daeb
f3f1f8
ecf7fb

Requirements
Must have
• Name, Title, Email, Mobile
Nice to have
• We have multiple locations in USA, KSA, EGY, so I need ideas about how to include all contact details maybe QR / Barcode or something else.
• Please see our locations and contact information: www.brightvelmora.example
Should not have
• Too much text

```html
<!DOCTYPE html>
<html lang="en">
<head>
<meta charset="utf-8">
<title>Velmora Company – January 2016 Calendar</title>
<link href="https://fonts.googleapis.com/css2?family=Arimo:wght@400;700&family=Jura:wght@500;600;700&display=swap" rel="stylesheet">
<style>
  :root {
    --navy: #0f2f5e;
    --ink: #111111;
    --muted: #b4b4b8;
    --holiday: #e0197d;
    --page-top: #d8d8da;
    --page-bottom: #ececee;
    --weekend-band: rgba(160, 160, 168, 0.22);
    --moon: #a8a8ae;
  }
  * { box-sizing: border-box; margin: 0; padding: 0; }
  html, body { width: 1200px; height: 1000px; overflow: hidden; background: #ffffff; }
  .sheet {
    position: absolute; left: 121px; top: 20px; width: 957px; height: 958px;
    box-shadow: 0 2px 8px rgba(0,0,0,0.45);
    background: linear-gradient(160deg, #dcdcde 0%, #f2f2f3 45%, #dedee0 70%, #ebebed 100%);
    overflow: hidden;
  }
  .hero {
    position: absolute; left: 0; top: 0; width: 957px; height: 500px;
    background:
      radial-gradient(circle at 66% 55%, #eeeeef 0%, #cfcfd2 28%, rgba(200,200,204,0) 40%),
      linear-gradient(90deg, #6f5646 0%, #9a8272 10%, #c9c6c6 30%, #d6d5d7 55%, #e9e9ea 80%, #f4f4f4 100%);
  }
  .brand {
    position: absolute; right: 30px; top: 48px;
    font-family: "Jura", sans-serif; font-weight: 700; font-size: 58px;
    letter-spacing: 2px; color: var(--navy); line-height: 1;
  }
  .month-title {
    position: absolute; left: 237px; top: 526px;
    font-family: "Jura", sans-serif; font-weight: 600; font-size: 33px;
    color: var(--navy); letter-spacing: 1px;
  }
  .weekend-band {
    position: absolute; top: 595px; width: 84px; height: 340px;
    background: var(--weekend-band);
  }
  .calendar { position: absolute; left: 0; top: 0; width: 957px; height: 958px; font-family: "Arimo", sans-serif; }
  .dow, .day {
    position: absolute; width: 80px; margin-left: -40px; text-align: center;
  }
  .dow { font-size: 10px; font-weight: 700; color: var(--ink); }
  .day { font-size: 17px; color: var(--ink); line-height: 1; }
  .day.other { color: var(--muted); }
  .note { display: block; font-size: 6px; margin-top: 4px; color: var(--ink); white-space: nowrap; }
  .note.holiday { color: var(--holiday); }
  .moon { position: absolute; width: 9px; height: 9px; margin-left: 14px; margin-top: -14px; }
  .services {
    position: absolute; left: 688px; top: 596px; list-style: none;
    font-family: "Jura", sans-serif; font-weight: 600; font-size: 17px;
    color: var(--navy); line-height: 26px;
  }
  .services li { margin-bottom: 28px; }
</style>
</head>
<body>
<div class="sheet">
  <div class="hero" role="img" aria-label="Photo of a frosted glass globe resting beside open book pages and white folders"></div>
  <div class="brand">VELMORA</div>

  <h1 class="month-title">JANUARY 2016</h1>

  <div class="weekend-band" style="left:34px"></div>
  <div class="weekend-band" style="left:562px"></div>

  <div class="calendar">
    <div class="dow" style="left:74px;top:597px">Sun</div>
    <div class="dow" style="left:162px;top:597px">Mon</div>
    <div class="dow" style="left:251px;top:597px">Tue</div>
    <div class="dow" style="left:339px;top:597px">Wed</div>
    <div class="dow" style="left:428px;top:597px">Thu</div>
    <div class="dow" style="left:517px;top:597px">Fri</div>
    <div class="dow" style="left:606px;top:597px">Sat</div>

    <!-- row 1 -->
    <div class="day other" style="left:74px;top:610px">27</div>
    <div class="day other" style="left:162px;top:610px">28</div>
    <div class="day other" style="left:251px;top:610px">29</div>
    <div class="day other" style="left:339px;top:610px">30</div>
    <div class="day other" style="left:428px;top:610px">31<span class="note">New Year's Eve</span></div>
    <div class="day" style="left:517px;top:610px">1<span class="note holiday">New Year's Day</span></div>
    <div class="day" style="left:606px;top:610px">2<svg class="moon" viewBox="0 0 10 10"><circle cx="5" cy="5" r="4.5" fill="none" stroke="var(--moon)"/><path d="M5 .5a4.5 4.5 0 0 1 0 9z" fill="var(--moon)"/></svg></div>

    <div class="day" style="left:74px;top:668px">3</div>
    <div class="day" style="left:162px;top:668px">4</div>
    <div class="day" style="left:251px;top:668px">5</div>
    <div class="day" style="left:339px;top:668px">6</div>
    <div class="day" style="left:428px;top:668px">7</div>
    <div class="day" style="left:517px;top:668px">8</div>
    <div class="day" style="left:606px;top:668px">9<svg class="moon" viewBox="0 0 10 10"><circle cx="5" cy="5" r="4.5" fill="var(--moon)"/></svg></div>

    <div class="day" style="left:74px;top:725px">10</div>
    <div class="day" style="left:162px;top:725px">11</div>
    <div class="day" style="left:251px;top:725px">12</div>
    <div class="day" style="left:339px;top:725px">13</div>
    <div class="day" style="left:428px;top:725px">14</div>
    <div class="day" style="left:517px;top:725px">15</div>
    <div class="day" style="left:606px;top:725px">16<svg class="moon" viewBox="0 0 10 10"><circle cx="5" cy="5" r="4.5" fill="none" stroke="var(--moon)"/><path d="M5 .5a4.5 4.5 0 0 0 0 9z" fill="var(--moon)"/></svg></div>

    <div class="day" style="left:74px;top:782px">17</div>
    <div class="day" style="left:162px;top:782px">18<span class="note holiday">Martin Luther King Day</span></div>
    <div class="day" style="left:251px;top:782px">19</div>
    <div class="day" style="left:339px;top:782px">20</div>
    <div class="day" style="left:428px;top:782px">21</div>
    <div class="day" style="left:517px;top:782px">22</div>
    <div class="day" style="left:606px;top:782px">23<svg class="moon" viewBox="0 0 10 10"><circle cx="5" cy="5" r="4.5" fill="none" stroke="var(--moon)"/></svg></div>

    <div class="day" style="left:74px;top:839px">24</div>
    <div class="day" style="left:162px;top:839px">25</div>
    <div class="day" style="left:251px;top:839px">26</div>
    <div class="day" style="left:339px;top:839px">27</div>
    <div class="day" style="left:428px;top:839px">28</div>
    <div class="day" style="left:517px;top:839px">29</div>
    <div class="day" style="left:606px;top:839px">30</div>

    <div class="day" style="left:74px;top:896px">31<svg class="moon" viewBox="0 0 10 10"><circle cx="5" cy="5" r="4.5" fill="none" stroke="var(--moon)"/><path d="M5 .5a4.5 4.5 0 0 1 0 9z" fill="var(--moon)"/></svg></div>
    <div class="day other" style="left:162px;top:896px">1</div>
    <div class="day other" style="left:251px;top:896px">2</div>
    <div class="day other" style="left:339px;top:896px">3</div>
    <div class="day other" style="left:428px;top:896px">4</div>
    <div class="day other" style="left:517px;top:896px">5</div>
    <div class="day other" style="left:606px;top:896px">6</div>
  </div>

  <ul class="services">
    <li>TECHNOLOGY SERVICE<br>MANAGEMENT</li>
    <li>EDUCATION SERVICES</li>
    <li>OUTSOURCING MANAGEMENT</li>
    <li>EVENTS MANAGEMENT</li>
  </ul>
</div>
</body>
</html>
```